i would like a business card to leave with customers and potential customers for electrical work and for the supply and install of reverse cycle airconditioning in the domestic and commercial market.
I own my own business and im a sole trader. I have an a'class electrical lisence and also a refrigeration lisence so i am
able to offer complete installations in airconditioning by a fully qualified and lisenced tradesman.
im looking for something that comes across as unique and professional.
i had the coluor black and some gold in mind but open to any coluors.
something like Lanterra Electrical & Refrigeration
or Lanterra Air.
i will use this design on a business card to advertise through summer to help generate installs through the busy season.

Target Market(s)

Mainly domestic house holds through summer who are in need of airconditioning and reliable information to acomadate thier cooling and heating requirements

Industry/Entity Type

Electrical

Requirements
Must have
• Business name- Lanterra
My name- Mark Delford
My mobile no- 0438 517 290
My email- mrdelford@qelvo.com.au
Installation & Decomissioning of aiconditioning split systems
LIC NO: TRK 540316
Nice to have
• Lanterra Electrical & Refrigeration

```html
<!DOCTYPE html>
<html lang="en">
<head>
<meta charset="utf-8">
<title>Lanterra Electrical &amp; Refrigeration – Business Card</title>
<link rel="stylesheet" href="https://fonts.googleapis.com/css2?family=Open+Sans:wght@400;600;700;800&family=Russo+One&display=swap">
<style>
  :root {
    --backdrop: #e9ecee;
    --card-gold: #dccb06;
    --card-black: #000000;
    --ink-dark: #111111;
    --ink-white: #ffffff;
    --mark-square: #2aa9e0;
    --badge-sky: #6fdcf7;
    --badge-lime: #b8f000;
  }
  * { box-sizing: border-box; margin: 0; padding: 0; }
  html, body { width: 1200px; height: 900px; overflow: hidden; }
  body {
    position: relative;
    background: var(--backdrop);
    font-family: "Open Sans", Arial, sans-serif;
  }
  .card {
    position: absolute;
    left: 244px;
    width: 712px;
    height: 405px;
    border-radius: 24px;
    overflow: hidden;
  }
  .card--front { top: 35px; background: var(--card-gold); }
  .card--back { top: 457px; background: var(--card-black); }

  /* Front */
  .brand-square {
    position: absolute;
    left: 40px; top: 108px;
    width: 92px; height: 92px;
    background: var(--mark-square);
  }
  .brand-name {
    position: absolute;
    left: 162px; top: 92px;
    font-weight: 800;
    font-size: 92px;
    line-height: 1;
    color: var(--ink-white);
    letter-spacing: -1px;
  }
  .brand-tagline {
    position: absolute;
    left: 336px; top: 201px;
    font-size: 14.5px;
    color: var(--ink-dark);
  }
  .contact-name {
    position: absolute;
    left: 0; width: 712px; top: 324px;
    text-align: center;
    font-family: "Russo One", Arial, sans-serif;
    font-size: 25px;
    line-height: 1.1;
    letter-spacing: 2px;
    color: var(--ink-dark);
  }
  .contact-phone {
    position: absolute;
    left: 0; width: 712px; top: 352px;
    text-align: center;
    font-size: 19px;
    letter-spacing: 0.6px;
    color: var(--ink-dark);
  }
  .contact-email {
    position: absolute;
    left: 686px; top: 197px;
    transform: translate(-50%, -50%) rotate(-90deg);
    white-space: nowrap;
    font-size: 16px;
    letter-spacing: 2.6px;
    color: var(--ink-dark);
  }

  /* Back */
  .service-line {
    position: absolute;
    left: 40px; top: 32px;
    font-weight: 700;
    font-size: 17px;
    line-height: 1.3;
    color: var(--ink-white);
  }
  .badge {
    position: absolute;
    left: 85px; top: 236px;
    width: 80px; height: 80px;
  }
  .licence {
    position: absolute;
    left: 40px; top: 353px;
    font-weight: 700;
    font-size: 16.5px;
    letter-spacing: 0.3px;
    color: var(--ink-white);
  }
  .brand-vertical {
    position: absolute;
    left: 652px; top: 203px;
    transform: translate(-50%, -50%) rotate(-90deg);
    white-space: nowrap;
    font-weight: 800;
    font-size: 80px;
    line-height: 1;
    letter-spacing: -0.5px;
    color: var(--card-gold);
  }
</style>
</head>
<body>
  <section class="card card--front" aria-label="Card front">
    <div class="brand-square" aria-hidden="true"></div>
    <div class="brand-name">Lanterra</div>
    <p class="brand-tagline">Lanterra Electrical &amp; Refrigeration</p>
    <p class="contact-name">Mark Delford</p>
    <p class="contact-phone">0438 517 290</p>
    <p class="contact-email">mrdelford@qelvo.com.au</p>
  </section>

  <section class="card card--back" aria-label="Card back">
    <p class="service-line">Installation &amp; Decommissioning<br>of air-conditioning split systems</p>
    <svg class="badge" viewBox="0 0 80 80" role="img" aria-label="Authorised installer badge">
      <rect x="0" y="0" width="80" height="80" fill="var(--badge-lime)"/>
      <polygon points="0,0 80,0 80,40 0,40" fill="var(--badge-sky)"/>
    </svg>
    <p class="licence">LIC NO: TRK 540316</p>
    <div class="brand-vertical">Lanterra</div>
  </section>
</body>
</html>
```